Stationery Design Project

We need a stationery design for our Norwegian trucking company. We have existed for about 15 years and our 12 drivers uses relatively new vehicles to transport goods around in northern Norway. Long distance routes with fresh fish og food transport is our main operations.

We have already made alogo that's printed on our trucks. The logo and a picture of our trucks is attached. I think the logo i crappy, but since its already in use, changing it is not an option in this round. Still using a better colour scheme in the overall stationery and more interesting fonts is possible (altso in the logo).

Company details:
Name: Kjelvraket AS
Organisation nr 873 615 309
Post adress: 8642 Raudvik

I like minimalism and simplicity. I am avalibly for questions in normal GMT working hours either here or on mail: ivar@fjordlast.no

Reason: Hi. Im extending the deadline because I needed some time to find a vector file of our logo. Sorry for the inconvenience

Hi, and thanks for all your interest in the project. Some updates:

-          I have decided to commit to using one of the designs. Some designer will get the payment.

-          I have extended the deadline with 24 hours since I needed some time to find our firms vector logo (a slow Swedish man was holding me up)

-          We will not choose a design before the deadline. No need to rush.

-          We have received a lot of great design and think there is a need to specified the product we want to make:

o   Business Card for all our employers. I just need the design and will duplicate with the correct numbers and name myself. The information on should be: Logo, employer’s name, Phone number, email, website, Postal number and address. Use this as a template: logo, Leif Brattvoll, 47382066, Leif@fjordlast.no,, fjordlast.no, 8642 Raudvik. The order and placement of the information is your creative decision.

o   Stickers to put on the goods we travel. On the sticker the should be the following information: Logo, phone number, Tekst and link: Fraktæ av Kjelvraket. Ke du syns? Fjordlast.no/tilbakemelding (this means: Handled by Kjelvraket. What do you think Fjordlast.no/feedback -à the link will be a feedback form). The placement the information and size is your creative decision with some stings: we have been thinking of using Drukko for printing and see that a size about 6x6 cm, 8x5 or something like that. (with 3000 copies our budget is 200 punds). Any suggestions of other suppliers are welcome. Drukko price calculator http://www.drukkolabelhouse.co.uk/digital-litho-printing/printing-labels-tags/stickers/

o   Letterhead with logo, address, phone number and organizational number.

o   Envelopes with logo,address, phone number and organizational number.

Have a nice day.

 

 

• Using the blue colour in the logo and using a similar graphic approch.

```html
<!DOCTYPE html>
<html lang="no">
<head>
<meta charset="utf-8">
<title>Kjelvraket AS – stationery</title>
<link rel="stylesheet" href="https://fonts.googleapis.com/css2?family=Arimo:wght@400;700&display=swap">
<style>
  :root {
    --band-blue: #5a5fc8;
    --ink-purple: #4a2190;
    --fresh-green: #5bbf2a;
    --paper: #ffffff;
    --sheet-edge: #9a9a9a;
    --body-ink: #2c2c2c;
    --label-ink: #1a1a1a;
  }
  * { box-sizing: border-box; margin: 0; padding: 0; }
  html, body { width: 1200px; height: 834px; overflow: hidden; }
  body {
    font-family: "Arimo", Arial, sans-serif;
    background: radial-gradient(ellipse at 50% 40%, #fafafa 0%, #e6e6e6 70%, #d9d9d9 100%);
    position: relative;
  }
  .item-label { position: absolute; font-size: 19px; color: var(--label-ink); }
  .paper { position: absolute; background: var(--paper); border: 1px solid var(--sheet-edge); overflow: hidden; }
  .wordmark {
    position: absolute; font-weight: 700; color: var(--ink-purple);
    display: flex; align-items: center; gap: 0.3em; white-space: nowrap;
  }
  .wordmark::before {
    content: ""; width: 0.55em; height: 0.55em; border-radius: 50%; background: var(--band-blue);
  }
  .contact { position: absolute; color: var(--ink-purple); white-space: nowrap; font-style: normal; }

  /* plain accent rules */
  .rule { position: absolute; background: var(--band-blue); }
  .rule--green { background: var(--fresh-green); }

  .sticker { position: absolute; left: 248px; top: 31px; width: 156px; height: 156px; }

  /* letterhead */
  .letterhead { left: 622px; top: 52px; width: 537px; height: 715px; }
  .letterhead .wordmark { left: 78px; top: 48px; font-size: 26px; }
  .letter-body {
    position: absolute; left: 76px; top: 162px; width: 372px;
    font-size: 8.3px; line-height: 11.4px; color: var(--body-ink); text-align: justify;
  }
  .letter-body p { margin-bottom: 11.4px; }
  .letter-body .closing { margin-bottom: 0; }
  .signature-area {
    position: absolute; left: 78px; top: 520px; width: 110px; height: 34px;
    background: linear-gradient(90deg, #f2f2f2, #e4e4e4);
  }
  .letterhead .contact { left: 308px; top: 640px; font-size: 10px; line-height: 12.2px; }

  /* envelope */
  .envelope { left: 56px; top: 232px; width: 533px; height: 267px; }
  .envelope .wordmark { left: 52px; top: 126px; font-size: 21px; }
  .envelope .contact { left: 53px; top: 176px; font-size: 10px; line-height: 12.6px; }

  /* cards */
  .card-front { left: 90px; top: 534px; width: 208px; height: 134px; }
  .card-front .wordmark { left: 98px; top: 18px; font-size: 12px; }
  .card-name { position: absolute; left: 16px; top: 81px; font-size: 10px; color: var(--ink-purple); }
  .card-role { position: absolute; left: 16px; top: 94px; font-size: 6.5px; color: var(--ink-purple); }
  .card-front .contact { left: 100px; top: 96px; font-size: 5.6px; line-height: 6.6px; }
  .card-back { left: 320px; top: 534px; width: 208px; height: 134px; }
  .card-back .wordmark { left: 38px; top: 52px; font-size: 19px; }
</style>
</head>
<body>

<span class="item-label" style="left:152px;top:108px;">sticker</span>
<span class="item-label" style="left:516px;top:58px;">letterhead</span>
<span class="item-label" style="left:74px;top:198px;">DL envelope</span>
<span class="item-label" style="left:74px;top:511px;">card front</span>
<span class="item-label" style="left:390px;top:511px;">back</span>

<svg class="sticker" viewBox="0 0 156 156" role="img" aria-label="Round feedback sticker">
  <defs>
    <path id="sticker-ring" d="M 16 78 A 62 62 0 1 1 140 78 A 62 62 0 1 1 16 78"/>
  </defs>
  <circle cx="78" cy="78" r="77" fill="var(--fresh-green)"/>
  <circle cx="78" cy="78" r="53" fill="#ffffff"/>
  <text font-family="Arimo, Arial, sans-serif" font-size="8.4" font-weight="700" fill="#ffffff">
    <textPath href="#sticker-ring" startOffset="2" textLength="380" lengthAdjust="spacing">Fraktæ av Kjelvraket. Ke du syns?  Tel. 47382066 • www.fjordlast.no/tilbakemelding</textPath>
  </text>
  <circle cx="45" cy="78" r="3.5" fill="var(--band-blue)"/>
  <text x="52" y="82.5" font-family="Arimo, Arial, sans-serif" font-size="13" font-weight="700" fill="var(--ink-purple)">Kjelvraket</text>
</svg>

<section class="paper letterhead">
  <div class="wordmark">Kjelvraket</div>
  <div class="rule" style="left:422px;top:0;width:4px;height:120px;"></div>
  <div class="rule rule--green" style="left:430px;top:0;width:4px;height:70px;"></div>
  <div class="letter-body">
    <p>Lorem ipsum dolor</p>
    <p>Sit amet, consectetur adipiscing elit. Sed justo dui, mollis sed hendrerit ut, sagittis eu tellus. Maecenas pellentesque orci vel ante ullamcorper sed luctus sem feugiat. Nunc auctor malesuada lacus, a lacinia tellus venenatis ac. Cum sociis natoque penatibus et magnis dis parturient montes, nascetur ridiculus mus. Etiam in imperdiet tortor. Vestibulum vestibulum nibh vitae enim adipiscing imperdiet sit amet non arcu. In hac habitasse platea dictumst. Nam massa augue, pulvinar ac sollicitudin elementum, rutrum vel turpis. Morbi hendrerit, magna ut placerat fringilla, odio arcu auctor risus, eu scelerisque ante tellus quis eros. Sed id consequat justo. Curabitur lacinia metus et purus laoreet in imperdiet sapien pretium. Donec sit amet iaculis augue. Donec vel augue nec ipsum interdum molestie. Nullam non lectus metus, vel sodales sem.</p>
    <p>Maecenas aliquet pulvinar nisl sit amet elementum. Nam velit massa, elementum eu cursus vel, congue vel quam. Mauris in diam viverra massa rutrum cursus. Nulla lacinia justo non mi pulvinar euismod. Cum sociis natoque penatibus et magnis dis parturient montes, nascetur ridiculus mus. Aliquam placerat accumsan tellus, nec euismod nibh vulputate eget. Quisque sollicitudin ultrices malesuada. In quis nisl tincidunt arcu iaculis feugiat.</p>
    <p>Donec ut ultrices urna. Vestibulum dignissim porttitor laoreet. Nunc gravida tincidunt venenatis. Etiam hendrerit arcu ac quam luctus a mattis nunc eleifend. Fusce ac interdum elit. Maecenas fermentum elit sit amet diam sodales vitae molestie arcu sodales. Aliquam non arcu sapien. Cum sociis natoque penatibus et magnis dis parturient montes, nascetur ridiculus mus. Integer eu sapien magna. Vestibulum aliquam tristique sem, in convallis arcu facilisis in. Sed sapien leo, aliquet vel accumsan eget, dapibus eget ligula.</p>
    <p>Aliquam euismod, nisl quis</p>
    <p class="closing">Cras pharetra<br>&nbsp;pretium enim,</p>
  </div>
  <div class="signature-area" role="img" aria-label="Handwritten signature"></div>
  <div class="rule" style="left:0;top:636px;width:270px;height:4px;"></div>
  <div class="rule rule--green" style="left:0;top:644px;width:180px;height:4px;"></div>
  <address class="contact">
    Kjelvraket AS<br>
    Organisation nr 873 615 309<br>
    8642 Raudvik - Norge<br>
    Tel. 0456 78 912 340<br>
    www.fjordlast.no
  </address>
</section>

<section class="paper envelope">
  <div class="rule" style="left:54px;top:0;width:4px;height:96px;"></div>
  <div class="rule rule--green" style="left:62px;top:0;width:4px;height:56px;"></div>
  <div class="wordmark">Kjelvraket</div>
  <div class="rule" style="left:280px;top:180px;width:253px;height:4px;"></div>
  <div class="rule rule--green" style="left:370px;top:188px;width:163px;height:4px;"></div>
  <address class="contact">
    Kjelvraket AS<br>
    Organisation nr 873 615 309<br>
    8642 Raudvik - Norge<br>
    Tel. 0456 78 912 340<br>
    www.fjordlast.no
  </address>
</section>

<section class="paper card-front">
  <div class="wordmark">Kjelvraket</div>
  <div class="card-name">Leif BRATTVOLL</div>
  <div class="card-role">Company Position</div>
  <div class="rule" style="left:0;top:107px;width:88px;height:2px;"></div>
  <div class="rule rule--green" style="left:0;top:111px;width:58px;height:2px;"></div>
  <address class="contact">
    Kjelvraket AS<br>
    8642 Raudvik - Norge<br>
    Tel. 47382066<br>
    leif@fjordlast.no<br>
    www.fjordlast.no
  </address>
</section>

<section class="paper card-back">
  <div class="rule" style="left:184px;top:0;width:3px;height:62px;"></div>
  <div class="rule rule--green" style="left:190px;top:0;width:3px;height:36px;"></div>
  <div class="wordmark">Kjelvraket</div>
</section>

</body>
</html>
```